Business card design for Automotive workshop

We need a business card for a new automotive repair and tyre shop called Keelstone Prime Automotive located in New Zealand. We are a clean, modern and fresh workshop and company.

Front needs to feature logo,
my name:
Marlo Fenwicke (director)

Address:
48 Tarn Lane
Harrowby 3627

Phone: 07 594 2713
Mobile: 027 451 9362
Email: office@keelstoneautomotive.example.nz
Website: keelstoneautomotive.example.nz

Back needs to feature an area to write down appointment details, date and time.

Also feature a list of jobs and work we do such as,
Vehicle Servicing
All Mechanical Repairs
Warrant of Fitness
Tyres & Wheel Alignments
Automotive Diagnostics
Automotive Parts & Supplies

```html
<!DOCTYPE html>
<html lang="en">
<head>
<meta charset="utf-8">
<title>Keelstone Prime Automotive – Business Card</title>
<link href="https://fonts.googleapis.com/css2?family=Open+Sans:ital,wght@0,400;0,600;0,700;1,600;1,700&display=swap" rel="stylesheet">
<style>
  :root {
    --bg: #3a3431;
    --card: #111111;
    --panel: #333333;
    --red: #e31b23;
    --white: #ffffff;
    --grey: #cfcfcf;
  }
  * { box-sizing: border-box; margin: 0; padding: 0; }
  html, body { width: 1200px; height: 795px; overflow: hidden; }
  body {
    background: var(--bg);
    font-family: "Open Sans", Arial, sans-serif;
    display: flex;
    align-items: center;
    justify-content: center;
    gap: 40px;
  }
  .card {
    position: relative;
    width: 560px;
    height: 320px;
    background: var(--card);
    overflow: hidden;
    box-shadow: 0 14px 30px rgba(0,0,0,.45);
  }

  /* Back side */
  .appointment-panel {
    position: absolute;
    left: 80px; top: 28px;
    width: 430px; height: 150px;
    background: var(--panel);
  }
  .appointment-title {
    position: absolute;
    left: 180px; right: 40px; top: 36px;
    text-align: center;
    color: var(--red);
    font-style: italic;
    font-weight: 700;
    font-size: 17px;
    letter-spacing: .5px;
  }
  .field {
    position: absolute;
    display: flex;
    align-items: flex-end;
    color: var(--white);
    font-style: italic;
    font-weight: 600;
    font-size: 13px;
  }
  .field .rule {
    flex: 1;
    border-bottom: 1px dashed var(--grey);
    margin-left: 6px;
    margin-bottom: 4px;
  }
  .field-date { left: 28px; top: 96px; width: 250px; }
  .field-time { left: 296px; top: 146px; width: 236px; }
  .services-band {
    position: absolute;
    left: 0; right: 0; bottom: 0;
    height: 120px;
    background: var(--red);
  }
  .services-label {
    position: absolute;
    left: 216px; top: 184px;
    background: var(--red);
    border: 2px solid var(--card);
    border-radius: 14px;
    padding: 2px 26px;
    color: var(--white);
    font-weight: 700;
    font-style: italic;
    font-size: 15px;
    z-index: 2;
  }
  .services-list {
    position: absolute;
    left: 28px; right: 20px; top: 242px;
    list-style: none;
    color: var(--white);
    font-style: italic;
    font-weight: 600;
    font-size: 12.5px;
    line-height: 25px;
  }
  .services-row { display: flex; gap: 12px; }
  .services-row.first { padding-left: 24px; }
  .services-row li::before { content: "• "; }

  /* Front side */
  .brand {
    position: absolute;
    right: 40px; top: 46px;
    width: 290px;
    text-align: center;
    color: var(--red);
    font-weight: 700;
    font-size: 22px;
    line-height: 1.15;
  }
  .person {
    position: absolute;
    right: 40px; top: 118px;
    width: 290px;
    text-align: center;
  }
  .person-name { color: var(--red); font-weight: 700; font-size: 21px; line-height: 1.2; }
  .person-role { color: var(--white); font-size: 13px; }
  .contacts {
    position: absolute;
    left: 24px; right: 24px; top: 184px;
    display: flex;
    justify-content: center;
    gap: 14px;
    color: var(--white);
    font-size: 12.5px;
  }
  .contact-col { display: flex; flex-direction: column; gap: 8px; }
  .contact-col.left { align-items: flex-end; }
  .contact-divider { width: 1px; background: var(--grey); }
  .contact-item { display: flex; align-items: center; gap: 5px; white-space: nowrap; }
  .contact-item svg { width: 11px; height: 11px; fill: var(--red); flex: none; }
  .address-band {
    position: absolute;
    left: 0; right: 0; bottom: 34px;
    height: 34px;
    background: var(--red);
    color: var(--white);
    font-size: 14px;
    display: flex;
    align-items: center;
    justify-content: center;
  }
</style>
</head>
<body>

  <section class="card card-back">
    <div class="appointment-panel"></div>
    <h2 class="appointment-title">Appointment Details</h2>
    <div class="field field-date">Date <span class="rule"></span></div>
    <div class="field field-time">Time <span class="rule"></span></div>
    <div class="services-band"></div>
    <div class="services-label">Our Works</div>
    <div class="services-list">
      <ul class="services-row first" style="list-style:none">
        <li>Vehicle Servicing</li>
        <li>Warrant of Fitness</li>
        <li>Automotive Parts &amp; Supplies</li>
      </ul>
      <ul class="services-row" style="list-style:none">
        <li>Automotive Diagnostics</li>
        <li>Tyres &amp; Wheel Alignments</li>
        <li>All Mechanical Repairs</li>
      </ul>
    </div>
  </section>

  <section class="card card-front">
    <div class="brand">Keelstone Prime Automotive</div>
    <div class="person">
      <div class="person-name">Marlo Fenwicke</div>
      <div class="person-role">Director</div>
    </div>
    <div class="contacts">
      <div class="contact-col left">
        <div class="contact-item">07 594 2713
          <svg viewBox="0 0 24 24"><path d="M6.6 10.8a15 15 0 0 0 6.6 6.6l2.2-2.2c.3-.3.7-.4 1-.2 1.1.4 2.3.6 3.6.6.6 0 1 .4 1 1V20c0 .6-.4 1-1 1A17 17 0 0 1 3 4c0-.6.4-1 1-1h3.5c.6 0 1 .4 1 1 0 1.3.2 2.5.6 3.6.1.3 0 .7-.2 1z"/></svg>
        </div>
        <div class="contact-item">office@keelstoneautomotive.example.nz
          <svg viewBox="0 0 24 24"><path d="M2 5h20v14H2z"/></svg>
        </div>
      </div>
      <div class="contact-divider"></div>
      <div class="contact-col">
        <div class="contact-item">
          <svg viewBox="0 0 24 24"><path d="M7 1h10a2 2 0 0 1 2 2v18a2 2 0 0 1-2 2H7a2 2 0 0 1-2-2V3a2 2 0 0 1 2-2zm0 3v14h10V4z"/></svg>027 451 9362
        </div>
        <div class="contact-item">
          <svg viewBox="0 0 24 24"><circle cx="12" cy="12" r="10"/></svg>keelstoneautomotive.example.nz
        </div>
      </div>
    </div>
    <div class="address-band">48 Tarn Lane Harrowby 3627</div>
  </section>

</body>
</html>
```